Real estate broker business card

Want a modern celan but effective business card for my residential and commercial real estate business. I want the back of the card to advertise my services and to capture business. I have attached the back of my current business card fore ideas
Updates

Logos, photo and text updates added! Added Saturday, September 3, 2016

Project Deadline Extended Reason: LOGOS, PHOTOS AND TEST JUST UPLOADED! I'M READY TO PICK A DESIGN! THANK YOU! Added Saturday, September 3, 2016

Target Market(s)

home buyers and seller. commercial buyers and sellers

Industry/Entity Type

Real Estate

Contact Information for Business Card

must have my contact information and my photo

Requirements
Must have
• Carla Ventrino
• Owner & Qualifying Broker
• Ventrino Real Estate Services
• 505.718.2094
• carla@ventrinohomes.example
• www.ventrinohomes.example
Nice to have
• metallic
• Business capture text: " Don't buy or lease property without someone looking out for your best interests. I will represent you on your home or investment purchase for FREE!"
• "Home owners, call today to receive a FREE market analysis for your homes value!

```html
<!DOCTYPE html>
<html lang="en">
<head>
<meta charset="utf-8">
<title>Ventrino Real Estate Services – Business Card</title>
<link rel="stylesheet" href="https://fonts.googleapis.com/css2?family=Cinzel:wght@400;600&family=Open+Sans:wght@400;600&display=swap">
<style>
  :root {
    --stage: #8a8a8a;
    --card: #ffffff;
    --teal: #2a8c93;
    --teal-dark: #1f6f76;
    --ink: #5a5f63;
    --photo-dark: #1f2a1c;
    --photo-mid: #3e4e35;
    --photo-light: #6b5a52;
  }
  * { box-sizing: border-box; margin: 0; padding: 0; }
  html, body { width: 1200px; height: 950px; overflow: hidden; }
  body {
    background: var(--stage);
    font-family: "Open Sans", Arial, sans-serif;
    display: flex;
    flex-direction: column;
    align-items: center;
    justify-content: center;
    gap: 50px;
  }
  .card {
    width: 700px;
    height: 400px;
    background: var(--card);
    box-shadow: 0 10px 30px rgba(0,0,0,.35);
    position: relative;
    overflow: hidden;
  }
  /* Front */
  .card--front { display: flex; }
  .portrait {
    width: 50%;
    height: 100%;
    background: radial-gradient(ellipse at 55% 60%, var(--photo-light) 0%, var(--photo-mid) 45%, var(--photo-dark) 100%);
  }
  .front-info {
    width: 50%;
    display: flex;
    flex-direction: column;
    align-items: center;
    justify-content: center;
    padding: 0 36px;
    text-align: center;
  }
  .brand-dot {
    width: 46px; height: 46px;
    border-radius: 50%;
    background: var(--teal);
    margin-bottom: 14px;
  }
  .brand-name {
    font-family: "Cinzel", Georgia, serif;
    font-weight: 400;
    color: var(--teal-dark);
    line-height: 1.1;
  }
  .brand-name .brand-main { display: block; font-size: 40px; letter-spacing: 1px; }
  .brand-name .brand-sub { display: block; font-size: 12px; letter-spacing: 3.5px; text-transform: uppercase; }
  .front-offer {
    margin-top: 34px;
    font-size: 15px;
    line-height: 1.45;
    color: var(--ink);
  }
  /* Back */
  .card--back {
    display: flex;
    flex-direction: column;
    align-items: center;
    justify-content: center;
    text-align: center;
    padding: 0 50px;
  }
  .agent-name {
    font-family: "Cinzel", Georgia, serif;
    font-weight: 400;
    font-size: 32px;
    letter-spacing: 1px;
    color: var(--teal);
    line-height: 1.2;
  }
  .agent-title { font-size: 17px; color: var(--ink); margin-top: 6px; }
  .contact { font-size: 16px; color: var(--ink); margin-top: 4px; line-height: 1.5; }
  .contact .label { color: var(--teal); font-weight: 600; }
  .divider {
    width: 460px; height: 1px;
    background: linear-gradient(90deg, transparent, var(--teal), transparent);
    margin: 16px 0;
  }
  .pitch { font-size: 15px; line-height: 1.45; color: var(--ink); max-width: 480px; }
</style>
</head>
<body>
  <section class="card card--front">
    <div class="portrait" role="img" aria-label="Portrait photo of Carla Ventrino outdoors against green foliage"></div>
    <div class="front-info">
      <span class="brand-dot"></span>
      <p class="brand-name"><span class="brand-main">Ventrino</span><span class="brand-sub">Real Estate Services</span></p>
      <p class="front-offer">Home owners, call today to<br>receive a FREE market<br>analysis for your homes value!</p>
    </div>
  </section>

  <section class="card card--back">
    <h1 class="agent-name">Carla Ventrino</h1>
    <p class="agent-title">Owner &amp; Qualifying Broker, Ventrino Real Estate Services</p>
    <p class="contact">
      <span class="label">P:</span> 505.718.2094 <span class="label">E:</span> carla@ventrinohomes.example<br>
      <span class="label">W:</span> www.ventrinohomes.example
    </p>
    <div class="divider"></div>
    <p class="pitch">Don't buy or lease property without someone looking out for your best interests. I will represent you on your home or investment purchase for FREE!</p>
  </section>
</body>
</html>
```